New business card, letter head, email signature and Portfolio for our Security company.

We are an Crest security company that provides a top quality manpower services to protect high rise buildings, retail and all type of properties and would like a new business card/logo look.

- We would like the spot UV design.
- Matt black (double sided).
- We would like to incorporate a royal blue colour (feel free to experiment with it).
- Feel free to try different lengths with the card to make it stand out more than a normal business card.
- We would like the logo to be an eagle eye in the background (shines when card is tilted slightly in the background, either on the front, back or both sides of the card). Image attached as an example of eye shape (colour to be either black or royal blue).
- HARBOUR CREST SECURITY SERVICES PTY. LTD. and HCSS to be placed on one side of the card and on the other side of the card to have;

- Name in slightly bigger font than the position (directly on the bottom on the name).
- Mobile number
- Email address
- Website email address
- PO BOX address

Can we please have the files in a format that we can edit.

Reason: I need to consult my business partner with the designs so far and will make a decision from there.

Target Market(s)

Security Industry

Industry/Entity Type

Business

Contact Information for Business Card

- Mobile number
- Email address
- Website email address
- PO BOX address

Logo Text

HCSS and underneath the HCSS please add HARBOUR CREST SECURITY SERVICES PTY. LTD.

Font styles to use
Other font styles liked:
• bold type font

Colors
0255a3
000000

Requirements
Must have
• We are an Crest security company that provides a top quality manpower services to protect high rise buildings, retail and all type of properties and would like a new business card/logo look.
• - We would like the spot UV design.
• - Matt black (double sided).
• - We would like to incorporate a royal blue colour (feel free to experiment with it).
• - Feel free to try different lengths with the card to make it stand out more than a normal business card.
• - We would like the logo to be an eagle eye in the background (shines when card is tilted slightly in the background, either on the front, back or both sides of the card). Image attached as an example of eye shape (colour to be either black or royal blue).
• - HARBOUR CREST SECURITY SERVICES PTY. LTD. and HCSS to be placed on one side of the card and on the other side of the card to have;
• - Name in slightly bigger font than the position (directly on the bottom on the name).
• - Mobile number
• - Email address
• - Website email address
• - PO BOX address
• Can we please have the files in a format that we can edit.
Nice to have
• Feel free to try different lengths with the card to make it stand out more than a normal business card.
• Please find "URBAN JUNGLE" font attached and incorporate HCSS into the same style with building's inside the HCSS bold front also add HARBOUR into the bottom part of the S and follow on E - Crest on the bottom S - SECURITY on the bottom S - SERVICES on the bottom of each letter.
• other than that, I'll be happy with a bold modern font for the HCSS and HARBOUR CREST SECURITY SERVICES in a bold and thinner font underneath.

```html
<!DOCTYPE html>
<html lang="en">
<head>
<meta charset="utf-8">
<title>Harbour Crest Security Services – Business Card</title>
<link rel="stylesheet" href="https://fonts.googleapis.com/css2?family=Anton&family=Noto+Sans:wght@400;700&display=swap">
<style>
  :root {
    --backdrop: #3b3430;
    --card-black: #111111;
    --card-edge: #1c1c1c;
    --spot-uv: #2e2e2e;
    --ink-white: #f2f2f2;
    --royal-blue: #0255a3;
    --divider: #5a5a5a;
  }
  * { margin: 0; padding: 0; box-sizing: border-box; }
  html, body {
    width: 1200px; height: 780px; overflow: hidden;
    background: var(--backdrop);
  }
  .canvas { position: relative; width: 1200px; height: 780px; }
  .card {
    position: absolute; width: 600px; height: 343px;
    background: var(--card-black);
    border: 1px solid var(--card-edge);
    box-shadow: 0 14px 30px rgba(0,0,0,.45);
  }
  .card--front { left: 40px; top: 40px; }
  .card--back { left: 560px; top: 397px; }

  .wordmark { position: absolute; text-align: center; font-family: "Anton", sans-serif; font-weight: 400; }
  .wordmark__initials { display: block; line-height: 1; letter-spacing: 6px; }
  .wordmark__name { display: block; letter-spacing: 1px; margin-top: 6px; }

  .card--front .wordmark { left: 0; right: 0; top: 92px; color: var(--spot-uv); }
  .card--front .wordmark__initials { font-size: 104px; }
  .card--front .wordmark__name { font-size: 21px; }

  .card--back .wordmark { left: 30px; width: 250px; top: 96px; color: var(--ink-white); }
  .card--back .wordmark__initials { font-size: 90px; }
  .card--back .wordmark__name { font-size: 17px; }

  .divider {
    position: absolute; left: 300px; top: 60px; width: 1px; height: 220px;
    background: var(--divider);
  }
  .contact {
    position: absolute; left: 325px; top: 70px; width: 260px;
    font-family: "Noto Sans", sans-serif; color: var(--ink-white);
  }
  .contact__name { font-size: 22px; font-weight: 700; line-height: 1.1; }
  .contact__role { font-size: 14px; color: var(--royal-blue); margin-bottom: 16px; }
  .contact__list { list-style: none; }
  .contact__item { display: flex; align-items: center; gap: 8px; font-size: 13.5px; line-height: 21px; }
  .contact__icon { width: 15px; height: 15px; flex: none; }
  .contact__address { font-size: 13.5px; line-height: 20px; margin-top: 10px; }
</style>
</head>
<body>
<main class="canvas">

  <section class="card card--front" aria-label="Card front">
    <div class="wordmark">
      <span class="wordmark__initials">HCSS</span>
      <span class="wordmark__name">HARBOUR CREST SECURITY SERVICES</span>
    </div>
  </section>

  <section class="card card--back" aria-label="Card back">
    <div class="wordmark">
      <span class="wordmark__initials">HCSS</span>
      <span class="wordmark__name">HARBOUR CREST SECURITY SERVICES</span>
    </div>
    <div class="divider"></div>
    <div class="contact">
      <p class="contact__name">Employee Name</p>
      <p class="contact__role">Manager</p>
      <ul class="contact__list">
        <li class="contact__item">
          <svg class="contact__icon" viewBox="0 0 15 15" aria-hidden="true">
            <rect width="15" height="15" fill="#0255a3"/>
            <rect x="5" y="3" width="5" height="9" rx="1" fill="none" stroke="#fff" stroke-width="1.2"/>
          </svg>0123 456 789</li>
        <li class="contact__item">
          <svg class="contact__icon" viewBox="0 0 15 15" aria-hidden="true">
            <rect width="15" height="15" fill="#0255a3"/>
            <rect x="3" y="4.5" width="9" height="6" fill="none" stroke="#fff" stroke-width="1.1"/>
            <path d="M3 4.5 L7.5 8.5 L12 4.5" fill="none" stroke="#fff" stroke-width="1.1"/>
          </svg>your@yourmail.net.nz</li>
        <li class="contact__item">
          <svg class="contact__icon" viewBox="0 0 15 15" aria-hidden="true">
            <rect width="15" height="15" fill="#0255a3"/>
            <circle cx="7.5" cy="7.5" r="4.5" fill="none" stroke="#fff" stroke-width="1.1"/>
            <path d="M3 7.5 H12 M7.5 3 V12" stroke="#fff" stroke-width="1"/>
          </svg>www.yourwebsite.co.nz</li>
      </ul>
      <p class="contact__address">P.O. Box 000, 2nd Lane<br>Kelso Bay, New Zealand</p>
    </div>
  </section>

</main>
</body>
</html>
```